Dalvick's Business Card

I need some designs for a new business card including the new logo attached. An old example of our business card is also attached to show all the data that should be included on the new design.
**I added some more examples someone had mocked up**

Contact Information for Business Card

Should include all info on other examples uploaded.

```html
<!DOCTYPE html>
<html lang="en">
<head>
<meta charset="utf-8">
<title>Dalvick's Business Card</title>
<link rel="stylesheet" href="https://fonts.googleapis.com/css2?family=Poppins:wght@400;600;700&family=Oswald:wght@500&display=swap">
<style>
  :root {
    --brand-blue: #0f72c2;
    --brand-red: #ec1c24;
    --card-white: #ffffff;
    --backdrop: #1f1f1f;
  }
  * { box-sizing: border-box; margin: 0; padding: 0; }
  html, body { width: 1200px; height: 1015px; overflow: hidden; }
  body {
    background: var(--backdrop);
    font-family: "Poppins", sans-serif;
    position: relative;
  }
  .card {
    position: absolute;
    left: 250px;
    width: 700px;
    height: 400px;
    background: var(--card-white);
    overflow: hidden;
  }
  .card-front { top: 70px; }
  .card-back { top: 545px; }

  /* Front */
  .brand {
    position: absolute;
    top: 70px;
    left: 0;
    width: 100%;
    display: flex;
    justify-content: center;
    align-items: center;
    gap: 18px;
  }
  .brand-dot {
    width: 64px; height: 64px;
    border-radius: 50%;
    background: var(--brand-blue);
  }
  .brand-text { display: flex; flex-direction: column; }
  .brand-name {
    font-weight: 700;
    font-size: 66px;
    line-height: 1;
    color: var(--brand-blue);
    letter-spacing: 2px;
  }
  .brand-tagline {
    font-size: 12.5px;
    font-weight: 400;
    color: var(--brand-red);
    letter-spacing: 1.6px;
    margin-top: 4px;
  }
  .band {
    position: absolute;
    left: 0;
    width: 100%;
    display: flex;
    align-items: center;
    justify-content: center;
    color: var(--card-white);
  }
  .band-area {
    top: 264px;
    height: 62px;
    background: var(--brand-red);
    font-weight: 700;
    font-size: 25px;
  }
  .band-services {
    top: 330px;
    height: 70px;
    background: var(--brand-blue);
    font-family: "Oswald", sans-serif;
    font-weight: 500;
    font-size: 25px;
    letter-spacing: 0.2px;
  }

  /* Back */
  .contact {
    position: absolute;
    left: 70px;
    top: 120px;
  }
  .person-name {
    font-weight: 700;
    font-size: 30px;
    color: var(--brand-red);
    letter-spacing: 1px;
  }
  .rule {
    width: 150px;
    height: 2px;
    background: var(--brand-blue);
    margin: 12px 0 14px;
  }
  .contact-row {
    display: flex;
    align-items: center;
    gap: 12px;
    font-size: 21px;
    color: var(--brand-blue);
    line-height: 1.35;
  }
  .contact-row svg { width: 22px; height: 22px; flex: none; }
  .credential {
    font-weight: 700;
    font-size: 20px;
    letter-spacing: 0.5px;
    line-height: 1.4;
  }
  .credential-licensed { color: var(--brand-blue); }
  .credential-family { color: var(--brand-red); }
  .back-mark {
    position: absolute;
    right: -60px;
    top: 40px;
    width: 330px;
    height: 330px;
    border-radius: 50%;
    background: var(--brand-blue);
  }
</style>
</head>
<body>
  <section class="card card-front">
    <div class="brand">
      <div class="brand-dot"></div>
      <div class="brand-text">
        <span class="brand-name">DALVICK'S</span>
        <span class="brand-tagline">AIR CONDITIONING &amp; HEATING SERVICE</span>
      </div>
    </div>
    <div class="band band-area">Serves Millbrook, IA &amp; Surrounding Areas</div>
    <div class="band band-services">CALL TODAY FOR ALL YOUR HVAC, REFRIGERATION &amp; PLUMBING NEEDS</div>
  </section>

  <section class="card card-back">
    <div class="contact">
      <h1 class="person-name">RAY DALVICK</h1>
      <div class="rule"></div>
      <div class="contact-row">
        <svg viewBox="0 0 24 24" aria-hidden="true"><path fill="var(--brand-red)" d="M6.6 10.8a15.1 15.1 0 0 0 6.6 6.6l2.2-2.2a1 1 0 0 1 1-.25 11.4 11.4 0 0 0 3.6.57 1 1 0 0 1 1 1V20a1 1 0 0 1-1 1A17 17 0 0 1 3 4a1 1 0 0 1 1-1h3.5a1 1 0 0 1 1 1c0 1.25.2 2.45.57 3.57a1 1 0 0 1-.25 1z"/></svg>
        <span>555.014.2287</span>
      </div>
      <div class="contact-row">
        <svg viewBox="0 0 24 24" aria-hidden="true"><rect x="2" y="5" width="20" height="14" fill="var(--brand-red)"/><path d="M2 5l10 8 10-8" fill="none" stroke="#fff" stroke-width="1.8"/></svg>
        <span>hvacdalvick@example.com</span>
      </div>
      <div class="rule"></div>
      <p class="credential credential-licensed">LICENSED &amp; INSURED</p>
      <p class="credential credential-family">FAMILY OWNED &amp; OPERATED</p>
    </div>
    <div class="back-mark"></div>
  </section>
</body>
</html>
```